BrivoTerna. Lantern of the Steady Harvest. Business card

Professional business card for BrivoTerna (Lantern of the Steady Harvest)
My rationale: Strategy-> Execution-> Results-> Value that lead to the BrivoTerna name: We put the Lantern of the Steady Harvest.
We deliver value to our customers helping them at defining a good strategy (cyan arrow). 90% of well formulated strategies fail due to poor execution so we also consider strategical execution very important (green arrow). Due to the execution we obtain the results (blue arrow). Finally, the results provide feedback to redefine strategy, and the new strategy has to be executed and new results obtained providing new feedback and on and on. It's like a wheel that finally, must create corporate value: value for shareholders, staholders, employees, providers...-

Target Market(s)

CEOs and steering comitees , invewrnent funds

Industry/Entity Type

Business Consultant

Contact Information for Business Card

Teodoro Vinsquel
CEO & Founder
teodoro.vinsquel@brivoterna-example.com
Mobile: +34 655.803.912
www.brivoterna-example.com

Colors

Designer to choose colors to be used in the design.

Requirements
Nice to have
• Nice to hace the words: Strategy, execution, results
• Nice to vave the claim: Lantern of the Steady Harvest
• The three colors should be shown:
• cyan for STRATEGY
• green for EXECUTION
• blue for RESULTS
Should not have
• Complete black background

```html
<!DOCTYPE html>
<html lang="en">
<head>
<meta charset="utf-8">
<title>BrivoTerna — Business Card</title>
<link rel="stylesheet" href="https://fonts.googleapis.com/css2?family=Source+Sans+3:wght@400;600;700&display=swap">
<style>
  :root {
    --stage-top: #e4e6e9;
    --stage-bottom: #b9bcc1;
    --card-white: #ffffff;
    --card-dark: #0b0b0b;
    --brand-blue: #1f3f94;
    --brand-green: #8dc63f;
    --brand-cyan: #27a9e1;
    --text-grey: #3a3a3a;
    --claim-white: #f2f2f2;
  }
  * { box-sizing: border-box; margin: 0; padding: 0; }
  html, body { width: 1200px; height: 800px; overflow: hidden; }
  body {
    background: linear-gradient(160deg, var(--stage-top), var(--stage-bottom));
    font-family: "Source Sans 3", sans-serif;
    display: flex;
    align-items: center;
    justify-content: center;
    gap: 90px;
  }
  .card {
    width: 330px;
    height: 560px;
    position: relative;
    overflow: hidden;
    box-shadow: 0 10px 28px rgba(0,0,0,0.25);
  }

  /* Front */
  .card-front { background: var(--card-white); }
  .brand {
    position: absolute;
    top: 70px; left: 0; right: 0;
    display: flex; align-items: center; justify-content: center; gap: 12px;
  }
  .brand-dot {
    width: 26px; height: 26px; border-radius: 50%;
    background: var(--brand-blue);
  }
  .brand-name {
    font-weight: 700; font-size: 44px; color: var(--brand-blue);
    letter-spacing: -0.5px;
  }
  .person {
    position: absolute; top: 250px; left: 0; right: 0; text-align: center;
  }
  .person-name { font-weight: 700; font-size: 22px; color: var(--brand-blue); }
  .person-role { font-size: 15px; color: var(--text-grey); margin-top: 2px; }
  .contact-icons {
    position: absolute; top: 358px; left: 0; right: 0;
    display: flex; justify-content: center; gap: 6px;
  }
  .contact-icons svg { width: 18px; height: 18px; }
  .contact-lines {
    position: absolute; top: 386px; left: 0; right: 0; text-align: center;
    font-size: 14.5px; line-height: 1.4; color: var(--text-grey);
  }
  .color-stripe {
    position: absolute; left: 0; right: 0; bottom: 0; height: 18px;
    display: flex;
  }
  .color-stripe span { flex: 1; }
  .stripe-blue { background: var(--brand-blue); }
  .stripe-green { background: var(--brand-green); }
  .stripe-cyan { background: var(--brand-cyan); }

  /* Back */
  .card-back { background: var(--card-dark); }
  .pillars-graphic {
    position: absolute; top: 30px; left: 24px; right: 24px; height: 420px;
    background: radial-gradient(ellipse at 30% 85%, rgba(39,169,225,0.35), transparent 60%),
                radial-gradient(ellipse at 50% 55%, rgba(141,198,63,0.35), transparent 60%),
                radial-gradient(ellipse at 40% 20%, rgba(31,63,148,0.55), transparent 65%);
    border-radius: 6px;
  }
  .pillar-words {
    position: absolute; top: 60px; left: 0; right: 0;
    display: flex; flex-direction: column; align-items: center; gap: 70px;
    font-weight: 700; font-size: 30px; letter-spacing: 3px;
  }
  .word-results { color: #6f8fe6; }
  .word-execution { color: var(--brand-green); }
  .word-strategy { color: var(--brand-cyan); }
  .claim {
    position: absolute; bottom: 44px; left: 0; right: 0; text-align: center;
    color: var(--claim-white); font-weight: 600; font-size: 14px;
    text-transform: uppercase; letter-spacing: 0.5px;
  }
</style>
</head>
<body>

  <section class="card card-front" aria-label="Business card front">
    <div class="brand">
      <span class="brand-dot"></span>
      <span class="brand-name">BrivoTerna</span>
    </div>

    <div class="person">
      <p class="person-name">Teodoro Vinsquel</p>
      <p class="person-role">CEO &amp; Founder</p>
    </div>

    <div class="contact-icons">
      <svg viewBox="0 0 18 18" aria-label="Phone">
        <circle cx="9" cy="9" r="9" fill="var(--brand-blue)"/>
        <rect x="6" y="4" width="6" height="10" rx="1" fill="none" stroke="#fff" stroke-width="1.3"/>
      </svg>
      <svg viewBox="0 0 18 18" aria-label="Email">
        <circle cx="9" cy="9" r="9" fill="var(--brand-green)"/>
        <rect x="4.5" y="5.5" width="9" height="7" fill="none" stroke="#fff" stroke-width="1.2"/>
        <path d="M4.5 5.5 L9 9.5 L13.5 5.5" fill="none" stroke="#fff" stroke-width="1.2"/>
      </svg>
      <svg viewBox="0 0 18 18" aria-label="Website">
        <circle cx="9" cy="9" r="9" fill="var(--brand-cyan)"/>
        <circle cx="9" cy="9" r="5" fill="none" stroke="#fff" stroke-width="1.1"/>
        <path d="M4 9 H14 M9 4 C6.5 6.5 6.5 11.5 9 14 M9 4 C11.5 6.5 11.5 11.5 9 14" fill="none" stroke="#fff" stroke-width="1"/>
      </svg>
    </div>

    <div class="contact-lines">
      <p>+34 655.803.912</p>
      <p>teodoro.vinsquel@brivoterna-example.com</p>
      <p>www.brivoterna-example.com</p>
    </div>

    <div class="color-stripe">
      <span class="stripe-blue"></span>
      <span class="stripe-green"></span>
      <span class="stripe-cyan"></span>
    </div>
  </section>

  <section class="card card-back" aria-label="Business card back">
    <div class="pillars-graphic" role="img" aria-label="Rising blue, green and cyan sweep symbolising strategy, execution and results"></div>
    <div class="pillar-words">
      <span class="word-results">RESULTS</span>
      <span class="word-execution">EXECUTION</span>
      <span class="word-strategy">STRATEGY</span>
    </div>
    <p class="claim">Lantern of the Steady Harvest</p>
  </section>

</body>
</html>
```